The most modern business card ever !!!

Our company call “Vendalo”. Vendalo is a technology company specialized in cruises solutions. Out main product is a platform to reserve cruises. This is a revolutionary platform that make easier to travel agencies and final users to reserve cruises across dozen companies like tibba, wernu, hpv, dgb, etc..We are a “start up”, with a young team of developers and we want to transmit it.. For it, we want something different, a modern business card that represent cruises and technology.. When someone receive this card, this person should say: wowww this is different… this is modern… this is a cruise related company..
- diferent, modern
- traditions business card

```html
<!DOCTYPE html>
<html lang="en">
<head>
<meta charset="utf-8">
<title>Vendalo — Business Card</title>
<link href="https://fonts.googleapis.com/css2?family=Montserrat:wght@400;500;600&family=Work+Sans:wght@400&display=swap" rel="stylesheet">
<style>
  :root {
    --canvas: #e9eaec;
    --card-white: #ffffff;
    --card-black: #151516;
    --accent: #29a8e0;
    --ink: #1b1b1d;
    --ink-soft: #2e2e30;
    --mark-grey: #4a4a4d;
  }
  * { margin: 0; padding: 0; box-sizing: border-box; }
  html, body {
    width: 1200px;
    height: 900px;
    overflow: hidden;
    background: var(--canvas);
  }
  .sheet {
    width: 1200px;
    height: 900px;
    display: flex;
    flex-direction: column;
    align-items: center;
    justify-content: center;
    gap: 24px;
  }
  .card {
    position: relative;
    width: 700px;
    height: 400px;
    box-shadow: 0 6px 18px rgba(0,0,0,0.18);
    overflow: hidden;
  }

  /* Front */
  .card-front {
    background: var(--card-white);
    border-bottom: 8px solid var(--accent);
    border-left: 4px solid var(--accent);
    font-family: "Work Sans", sans-serif;
    color: var(--ink);
  }
  .brand-name {
    position: absolute;
    top: 36px;
    right: 44px;
    font-family: "Montserrat", sans-serif;
    font-weight: 500;
    font-size: 54px;
    letter-spacing: 1px;
    color: var(--ink);
  }
  .person {
    position: absolute;
    left: 44px;
    top: 188px;
  }
  .person-name {
    font-family: "Montserrat", sans-serif;
    font-weight: 600;
    font-size: 24px;
    letter-spacing: 1.5px;
    color: var(--accent);
  }
  .person-role {
    margin-top: 4px;
    font-size: 15px;
    letter-spacing: 1px;
    color: var(--ink-soft);
  }
  .divider {
    position: absolute;
    left: 44px;
    right: 60px;
    top: 260px;
    height: 1.5px;
    background: var(--accent);
  }
  .address {
    position: absolute;
    right: 56px;
    top: 196px;
    text-align: right;
    font-size: 15px;
    line-height: 1.5;
    letter-spacing: 1px;
    color: var(--ink-soft);
  }
  .contacts {
    position: absolute;
    left: 44px;
    top: 282px;
    list-style: none;
    font-size: 16px;
    line-height: 1.55;
    letter-spacing: 1px;
    color: var(--ink-soft);
  }
  .contacts li {
    display: flex;
    align-items: center;
    gap: 10px;
  }
  .contact-icon {
    width: 12px;
    height: 12px;
    flex: none;
  }

  /* Back */
  .card-back {
    background: var(--card-black);
    display: flex;
    align-items: center;
    justify-content: center;
  }
  .back-name {
    font-family: "Montserrat", sans-serif;
    font-weight: 500;
    font-size: 92px;
    letter-spacing: 3px;
    color: var(--mark-grey);
  }
</style>
</head>
<body>
<main class="sheet">
  <section class="card card-front" aria-label="Business card front">
    <div class="brand-name">Vendalo</div>

    <div class="person">
      <div class="person-name">DANIEL FENWICK</div>
      <div class="person-role">Director</div>
    </div>

    <address class="address">
      214b Harlow Street,<br>
      Westbrook, NZ, 4620
    </address>

    <div class="divider"></div>

    <ul class="contacts">
      <li>
        <svg class="contact-icon" viewBox="0 0 24 24" aria-hidden="true">
          <path fill="#29a8e0" d="M6.6 10.8c1.4 2.8 3.8 5.1 6.6 6.6l2.2-2.2c.3-.3.7-.4 1-.2 1.1.4 2.3.6 3.6.6.6 0 1 .4 1 1V20c0 .6-.4 1-1 1C10.6 21 3 13.4 3 4c0-.6.4-1 1-1h3.5c.6 0 1 .4 1 1 0 1.3.2 2.5.6 3.6.1.3 0 .7-.2 1z"/>
        </svg>
        (555) 013-4821
      </li>
      <li>
        <svg class="contact-icon" viewBox="0 0 24 24" aria-hidden="true">
          <path fill="none" stroke="#29a8e0" stroke-width="2.2" d="M3 6h18v12H3z M3 6l9 7 9-7"/>
        </svg>
        info@vendalo.com.br
      </li>
      <li>
        <svg class="contact-icon" viewBox="0 0 24 24" aria-hidden="true">
          <circle cx="12" cy="12" r="9" fill="none" stroke="#29a8e0" stroke-width="2.2"/>
          <path fill="none" stroke="#29a8e0" stroke-width="2" d="M3 12h18M12 3c3 3 3 15 0 18M12 3c-3 3-3 15 0 18"/>
        </svg>
        www.vendalo.com.br
      </li>
    </ul>
  </section>

  <section class="card card-back" aria-label="Business card back">
    <div class="back-name">Vendalo</div>
  </section>
</main>
</body>
</html>
```